Garland Custom Boats Website update

I would like an updated website to my current site (Garlandboats.com).
I have an updated logo i would like to incorporate.
24 pages , would like to integrate videos of the boats (that i can upload later)

Target Market(s)

Professional and Commercial boat owners

Industry/Entity Type

Custom Boat Manufacturing

Coding

Coded - Design and coding required

Number of Pages Required

5+ page

Font styles to use
Serif

Requirements
Must have
• Easy to read, well laid-out, and video integration
Nice to have
• Fresh up to date look

```html
<!DOCTYPE html>
<html lang="en">
<head>
<meta charset="utf-8">
<title>Garland Custom Boats</title>
<link href="https://fonts.googleapis.com/css2?family=Jost:wght@300;400;500;700&family=Exo+2:wght@300;400&family=Cormorant+Garamond:wght@500&display=swap" rel="stylesheet">
<style>
:root{
  --red:#d7262e;
  --blue:#1c3f9c;
  --navy:#0f2236;
  --paper:#eef0f4;
  --ink:#222833;
  --muted:#4b5360;
  --white:#ffffff;
}
*{margin:0;padding:0;box-sizing:border-box}
html,body{width:1200px;height:4422px;overflow:hidden}
body{position:relative;background:var(--paper);font-family:"Jost",sans-serif;color:var(--ink)}
.abs{position:absolute}

.header{left:0;top:0;width:1200px;height:100px;background:var(--white)}
.logo{color:var(--blue);font-weight:700;font-size:26px;line-height:1;display:flex;align-items:center;gap:10px}
.logo .mark{width:16px;height:16px;background:var(--blue)}
.logo small{display:block;font-size:12px;font-weight:700;letter-spacing:2px;margin-top:4px}
.util{left:420px;top:0;width:680px;height:40px;border-bottom:1px solid #e3e5ea;display:flex;justify-content:flex-end;align-items:center;font-size:12px}
.util span{padding:0 14px;border-left:1px solid #c8ccd3}
.util span:first-child{border-left:none}
.nav{left:425px;top:56px;display:flex;gap:34px;font-size:12px;align-items:center;height:32px}
.nav .active{color:var(--red)}
.search{width:13px;height:13px;border:2px solid #555;border-radius:50%}
.btn-blue{left:963px;top:55px;width:137px;height:33px;background:var(--blue);color:#fff;font-size:12px;display:flex;align-items:center;justify-content:center;border-radius:2px}
.btn{background:var(--red);color:#fff;font-size:12px;display:flex;align-items:center;justify-content:center;border-radius:3px}

.hero{left:0;top:100px;width:1200px;height:540px;background:linear-gradient(180deg,#c9d6e4 0%,#6f93bb 30%,#1f4d92 55%,#173f86 100%)}
.hero-boat{left:690px;top:90px;width:330px;height:230px;background:radial-gradient(ellipse at center,#e9eef4 0%,#aab8c8 45%,rgba(40,80,140,0) 72%)}
.hero-title{left:100px;top:205px;font-family:"Exo 2",sans-serif;font-weight:300;font-size:54px;line-height:57px;color:#fff;letter-spacing:1px}
.hero-text{left:100px;top:335px;font-size:12.5px;line-height:19px;color:#fff}

.label{font-size:17px;color:var(--red);display:flex;align-items:center;gap:14px;font-weight:300}
.label i{display:block;width:110px;height:2px;background:linear-gradient(90deg,rgba(215,38,46,0),var(--red),rgba(215,38,46,0))}
.h2{font-family:"Exo 2",sans-serif;font-weight:300;font-size:34px;line-height:46px;color:var(--ink)}
.body{font-size:12.5px;line-height:20px;color:var(--muted);font-weight:300}
.photo{background:linear-gradient(160deg,#7eb3da 0%,#dfe9ef 35%,#5aa7a0 70%,#2f7e77 100%)}

.dark-band{left:0;width:1200px;background:linear-gradient(180deg,#2a3a3c 0%,#16283a 40%,#0c1f33 100%)}
.section-label{left:0;width:1200px;display:flex;justify-content:center;align-items:center;gap:14px;color:#fff;font-size:16px;font-weight:300}
.section-label i{display:block;width:110px;height:2px;background:linear-gradient(90deg,rgba(255,255,255,0),#fff,rgba(255,255,255,0))}
.section-title{left:0;width:1200px;text-align:center;color:#fff}
.section-intro{left:0;width:1200px;text-align:center;color:#d7dde6;font-size:12px;line-height:20px;font-weight:300}

.card{width:241px;height:250px;background:linear-gradient(180deg,#7fa4c6 0%,#dfe6ec 45%,#6f8aa5 100%)}
.card-label{width:241px;text-align:center;font-family:"Cormorant Garamond",serif;font-weight:500;font-size:17px;color:#fff}

.video{left:228px;top:2000px;width:744px;height:408px;border:2px solid #1a1f26;background:linear-gradient(180deg,#4b8fd1 0%,#cfe1ef 40%,#8aa59c 60%,#1c8a86 100%)}
.play{left:583px;top:2187px;width:34px;height:34px;border-radius:50%;background:var(--blue);display:flex;align-items:center;justify-content:center}

.list li{list-style:none;display:flex;gap:16px;font-size:17px;line-height:24px;margin-bottom:13px;color:var(--ink)}
.dot{flex:0 0 18px;height:18px;border:2px solid var(--red);border-radius:50%;margin-top:3px;display:flex;align-items:center;justify-content:center}
.dot::after{content:"";width:8px;height:8px;background:var(--red);border-radius:50%}

.cta{left:195px;top:3768px;width:810px;height:277px}
.cta-text{left:330px;top:3800px;color:#fff}

.footer-col h4{font-size:11px;font-weight:400;letter-spacing:.5px;color:var(--ink);margin-bottom:22px}
.footer-col a{display:block;font-size:12px;line-height:20px;color:var(--muted)}
.contact-row{display:flex;gap:10px;font-size:12px;line-height:20px;color:var(--muted);margin-bottom:10px}
.ico{flex:0 0 14px;height:14px;border:1px solid #666;border-radius:50%;margin-top:3px}
.social{display:flex;gap:10px}
.social span{width:24px;height:24px;border-radius:50%;background:var(--red)}
</style>
</head>
<body>

<header class="abs header">
  <div class="abs logo" style="left:100px;top:26px"><span class="mark"></span><div>GARLAND<small>CUSTOM BOATS</small></div></div>
  <div class="abs util"><span>Optional Equipment</span><span>US Coast Guard Package</span><span>Links</span><span>Driving Directions</span></div>
  <nav class="abs nav"><span class="active">Home</span><span>About Us</span><span>Boat Models ⌄</span><span>Boat Types ⌄</span><span>Gallery</span><span>Contact Us</span><span class="search"></span></nav>
  <div class="abs btn-blue">Let's Build Your Boat</div>
</header>

<section class="abs hero">
  <div class="abs hero-boat" role="img" aria-label="Custom sport fishing boat cruising across open water"></div>
  <h1 class="abs hero-title">Crafting Custom Boats<br>Since 1982</h1>
  <p class="abs hero-text">From recreational sport fishers to rugged dive and research vessels,<br>every Garland boat is built to exceed expectations.</p>
  <div class="abs btn" style="left:100px;top:395px;width:137px;height:33px">Explore Our Boats</div>
</section>

<section class="about">
  <div class="abs photo" style="left:108px;top:730px;width:477px;height:455px;clip-path:polygon(0 0,100% 0,86% 92%,78% 100%,0 100%)" role="img" aria-label="White motor yacht moored in turquoise water beside tropical trees"></div>
  <div class="abs label" style="left:620px;top:763px">Our Story Garland Boats <i></i></div>
  <h2 class="abs h2" style="left:622px;top:800px">More Than a Boat Builder –<br>A Legacy of Craftsmanship</h2>
  <p class="abs body" style="left:618px;top:905px;width:478px">Welcome to Garland Boats. We build custom boats to meet our customers' specification. Our boats range in size from 26' to 71'. We specialize in Dive Boats, Yacht Sport Fisherman, Patrol Boats, and Research Vessels. Our projects are original and diverse. Quality and customer satisfaction are always our top priorities.</p>
  <p class="abs body" style="left:618px;top:993px;width:478px">Founded in Bayport, Louisiana, Garland Boats is a second-generation, family-owned builder of custom fiberglass vessels. For over 40 years, we've worked closely with clients to design and construct boats that meet the highest standards of quality, durability, and performance. Each boat is a reflection of our commitment to hard work, attention to detail, and lifelong passion for the water.</p>
  <div class="abs btn" style="left:618px;top:1113px;width:160px;height:34px">Learn More About Us</div>
</section>

<section class="build">
  <div class="abs dark-band" style="top:1290px;height:820px" role="img" aria-label="Dark coastal cliffs above calm water"></div>
  <div class="abs section-label" style="top:1413px"><i></i>Tailored Vessels for Every Mission<i></i></div>
  <h2 class="abs h2 section-title" style="top:1443px">What We Build</h2>
  <p class="abs section-intro" style="top:1497px">Welcome to Garland Boats. We build custom boats to meet our customers' specification. Our boats range in<br>size from 26' to 71'. We specialize in Dive Boats, Yacht Sport Fisherman, Patrol Boats, and Research Vessels.<br>Our projects are original and diverse. Quality and customer satisfaction are always our top priorities.</p>
  <div class="abs card" style="left:100px;top:1592px" role="img" aria-label="Dive boat docked at a marina"></div>
  <div class="abs card" style="left:353px;top:1592px;background:linear-gradient(180deg,#3f8fd6,#e6eef4 55%,#2f6fb2)" role="img" aria-label="Sport fisher on open blue water"></div>
  <div class="abs card" style="left:606px;top:1592px;background:linear-gradient(180deg,#5d7e63,#e9ecee 55%,#7b8c96)" role="img" aria-label="Research vessel at the dock"></div>
  <div class="abs card" style="left:859px;top:1592px;background:linear-gradient(180deg,#cfd6dc,#8fa0ad 60%,#5c6770)" role="img" aria-label="Deck of a tour and glass bottom boat"></div>
  <div class="abs card-label" style="left:100px;top:1855px">Dive Boats</div>
  <div class="abs card-label" style="left:353px;top:1855px">Sport Fishers</div>
  <div class="abs card-label" style="left:606px;top:1855px">Research Vessels</div>
  <div class="abs card-label" style="left:859px;top:1855px">Tour &amp; Glass Bottom Boats</div>
  <div class="abs btn" style="left:531px;top:1905px;width:138px;height:32px">Explore Our Boats</div>
</section>

<div class="abs video" role="img" aria-label="Video of custom boats moored at a waterfront marina"></div>
<div class="abs play"><svg width="12" height="14" viewBox="0 0 12 14"><path d="M1 1 L11 7 L1 13 Z" fill="#fff"/></svg></div>

<section class="advantages">
  <div class="abs label" style="left:100px;top:2550px">Our Advantages <i></i></div>
  <h2 class="abs h2" style="left:104px;top:2584px">Why Choose Garland?</h2>
  <ul class="abs list" style="left:100px;top:2652px">
    <li><span class="dot"></span>Custom-Built in the USA</li>
    <li><span class="dot"></span>Top-Tier Power Options<br>(Marlow, Kestrel, Tidewell, etc.)</li>
    <li><span class="dot"></span>Built for Certification (USCG-ready)</li>
    <li><span class="dot"></span>Proven by Dive Operators, Universities, and State Agencies</li>
    <li><span class="dot"></span>Built to Last. Backed by Reputation.</li>
  </ul>
  <div class="abs btn" style="left:100px;top:2880px;width:159px;height:32px">Get A Quote</div>
  <div class="abs photo" style="left:624px;top:2504px;width:476px;height:456px;background:linear-gradient(160deg,#2c5877 0%,#9a8d6b 35%,#e8ecef 60%,#4c6d85 100%);clip-path:polygon(4% 0,100% 0,100% 100%,0 100%,0 22%)" role="img" aria-label="White flybridge sportfishing boat against a rocky hillside"></div>
</section>

<section class="featured">
  <div class="abs dark-band" style="top:3060px;height:790px" role="img" aria-label="Dark coastal cliffs above calm water"></div>
  <div class="abs section-label" style="top:3176px"><i></i>Tailored Vessels for Every Mission<i></i></div>
  <h2 class="abs h2 section-title" style="top:3206px">Featured Builds</h2>
  <p class="abs section-intro" style="top:3260px">Welcome to Garland Boats. We build custom boats to meet our customers' specification. Our boats range in<br>size from 26' to 71'. We specialize in Dive Boats, Yacht Sport Fisherman, Patrol Boats, and Research Vessels.<br>Our projects are original and diverse. Quality and customer satisfaction are always our top priorities.</p>
  <div class="abs card" style="left:100px;top:3355px;background:linear-gradient(180deg,#b9c3cc,#eef0f2 55%,#7d8790)" role="img" aria-label="71 foot custom dive boat in a city marina"></div>
  <div class="abs card" style="left:353px;top:3355px;background:linear-gradient(180deg,#3d7fc4,#e7eef3 50%,#4f9c93)" role="img" aria-label="53 foot sport fish boat"></div>
  <div class="abs card" style="left:606px;top:3355px;background:linear-gradient(180deg,#8aa8c4,#e6e9ec 50%,#8896a2)" role="img" aria-label="46 foot research vessel at the dock"></div>
  <div class="abs card" style="left:859px;top:3355px;background:linear-gradient(180deg,#8fb1d2,#d8e2ea 55%,#4c6f93)" role="img" aria-label="36 foot glass bottom boat on the water"></div>
  <div class="abs card-label" style="left:100px;top:3618px">71' Custom Dive</div>
  <div class="abs card-label" style="left:353px;top:3618px">53' Sport Fish</div>
  <div class="abs card-label" style="left:606px;top:3618px">46' Research Vessel</div>
  <div class="abs card-label" style="left:859px;top:3618px">36' Glass Bottom Boat</div>
  <div class="abs btn" style="left:531px;top:3668px;width:138px;height:32px">View All Models</div>
</section>

<section class="contact-cta">
  <svg class="abs cta" viewBox="0 0 810 277" preserveAspectRatio="none">
    <polygon points="0,0 810,0 770,277 40,277" fill="#c9222a"/>
    <polygon points="14,0 772,0 742,277 62,277" fill="#1a47a6"/>
  </svg>
  <div class="abs" style="left:560px;top:3790px;width:360px;height:240px;background:radial-gradient(ellipse at center,#e6ebf0 0%,#9fb0c3 45%,rgba(26,71,166,0) 72%)" role="img" aria-label="Custom cruiser under way on the water"></div>
  <div class="abs cta-text">
    <div style="display:flex;gap:14px;align-items:center;font-size:16px;font-weight:300">Get In Touch <span style="display:block;width:110px;height:2px;background:#fff"></span></div>
    <h2 class="h2" style="color:#fff;margin-top:8px;margin-left:8px">Start Your<br>Custom Build Today</h2>
    <p style="font-size:12px;font-weight:300;margin-top:6px">Let's design the boat you've always wanted.</p>
  </div>
  <div class="abs btn" style="left:330px;top:3958px;width:137px;height:32px">Explore Our Boats</div>
</section>

<footer>
  <div class="abs logo" style="left:100px;top:4130px"><span class="mark"></span><div>GARLAND<small>CUSTOM BOATS</small></div></div>
  <p class="abs body" style="left:100px;top:4225px;width:320px;font-size:12px;line-height:17px">If you don't see what you are looking for....ASK.<br>We can customize your boat to suit your needs.<br>Make sure you check out our links for more pictures<br>of our boats in use! Our boats can be USCG certified</p>
  <div class="abs footer-col" style="left:513px;top:4116px">
    <h4>QUICKS LINKS</h4>
    <a>Home</a><a>About Us</a><a>Boat Models</a><a>Boat Types</a><a>Gallery</a><a>Contact Us</a>
  </div>
  <div class="abs footer-col" style="left:700px;top:4116px">
    <h4>CONTACT INFO</h4>
    <div class="contact-row"><span class="ico"></span>(555) 210-4471</div>
    <div class="contact-row"><span class="ico"></span>office@garlandboats.com</div>
    <div class="contact-row"><span class="ico"></span>Garland Boats, Inc.<br>1420 Harbor Rd.<br>Bayport, LA 70999 &nbsp;USA</div>
  </div>
  <div class="abs footer-col" style="left:970px;top:4116px">
    <h4>SOCIAL LINKS</h4>
    <div class="social"><span></span><span></span><span></span><span></span></div>
  </div>
  <div class="abs" style="left:0;top:4352px;width:1200px;height:1px;background:#cfd3da"></div>
  <div class="abs" style="left:0;top:4383px;width:1200px;text-align:center;font-size:12px;color:var(--muted)">© Copyright All Right Reserved 2025</div>
</footer>

</body>
</html>
```